Can you make a cool and versatile Tarn Meridian Powerpoint template?
See www.tarnmeridian-example.co.uk and http://www.examplenet.invalid/company/tarn-meridian-ltd/ (on the right) to see how the logos are currently used - with interchangeably white and black backgrounds.
Target Market(s)
Marketing managers, product managers in HR technology, HR consultants
Industry/Entity Type
It Company
Font styles to use
Sans Serif
Requirements
Must have
- Master slide design, fonts, color theme, etc. Ideally two variations - one with white background (using colorful logo), one with a darker background (using black/white logo).

```html
<!DOCTYPE html>
<html lang="en">
<head>
<meta charset="utf-8">
<title>Tarn Meridian – Presentation Template</title>
<link rel="stylesheet" href="https://fonts.googleapis.com/css2?family=Graduate&family=PT+Sans:wght@400;700&display=swap">
<style>
  :root{
    --blue:#29a8e0;
    --blue-deep:#1b8fc4;
    --frame:#3a3a3c;
    --band:#39393b;
    --ink:#1d1d1f;
    --paper-a:#f4f4f4;
    --paper-b:#d9d9d9;
    --white:#ffffff;
    --muted:#b8b8b8;
    --display:"Graduate", serif;
    --text:"PT Sans", sans-serif;
  }
  *{margin:0;padding:0;box-sizing:border-box}
  html,body{width:1200px;height:900px;overflow:hidden;background:var(--white)}
  body{position:relative;font-family:var(--text);color:var(--ink)}

  .frame{position:absolute;background:var(--frame)}
  .slide{position:absolute;overflow:hidden;
    background:radial-gradient(ellipse at 40% 30%,var(--paper-a) 0%,#e6e6e6 55%,var(--paper-b) 100%)}

  /* title slide */
  .frame--title{left:9px;top:257px;width:758px;height:438px}
  .slide--title{left:26px;top:271px;width:726px;height:409px}
  .title-heading{position:absolute;left:166px;top:28px;font-family:var(--display);font-size:74px;
    line-height:1;color:var(--blue);letter-spacing:2px;white-space:nowrap}
  .title-details{position:absolute;left:176px;top:103px;font-size:16px;color:var(--ink);white-space:nowrap;letter-spacing:.2px}
  .reflection{position:absolute;left:0;top:0;width:100%;transform-origin:0 128px;transform:scaleY(-1);opacity:.18}
  .reflection .title-heading{top:42px}
  .reflection .title-details{top:110px}
  .brand-circle{position:absolute;left:299px;top:195px;width:154px;height:154px;border-radius:50%;
    background:var(--blue);border:4px solid var(--white);box-shadow:0 0 0 2px var(--blue);
    display:flex;align-items:center;justify-content:center}
  .brand-name{font-family:var(--text);font-weight:400;color:var(--white);font-size:16px}
  .title-url{position:absolute;left:0;width:748px;top:370px;text-align:center;font-size:17px;color:var(--ink)}
  .corner{position:absolute;width:64px;height:64px}
  .corner--br{right:14px;bottom:14px;background:var(--blue);clip-path:polygon(100% 0,100% 100%,0 100%)}
  .corner--br span{position:absolute;right:6px;bottom:2px;font-family:var(--display);color:var(--white);font-size:24px}

  /* side slides */
  .frame--stack{left:770px;top:120px;width:392px;height:704px}
  .slide--photo{left:780px;top:131px;width:370px;height:209px}
  .slide--bullets{left:778px;top:360px;width:380px;height:215px}
  .slide--graphic{left:778px;top:595px;width:380px;height:220px}
  .corner--tr{right:0;top:0;width:35px;height:35px;background:var(--blue);clip-path:polygon(0 0,100% 0,100% 100%)}
  .corner--tr span{position:absolute;right:4px;top:4px;font-family:var(--display);color:var(--white);font-size:8px}

  .photo{position:absolute;left:7px;top:10px;width:206px;height:137px;border:3px solid var(--frame);
    background:linear-gradient(120deg,#3a2a1c 0%,#b5501a 30%,#f6a31c 55%,#f9d35a 70%,#c96a12 100%)}

  .footer-band{position:absolute;left:4px;right:4px;height:48px;background:var(--band)}
  .footer-title{position:absolute;left:6px;top:5px;font-family:var(--display);font-size:22px;color:var(--blue);
    line-height:1;border-bottom:2px solid var(--blue);padding-bottom:1px;white-space:nowrap}
  .footer-sub{position:absolute;left:24px;top:33px;font-size:7px;color:var(--white);letter-spacing:.3px;white-space:nowrap}
  .footer-sub--right{left:104px}
  .footer-contact{position:absolute;left:262px;top:17px;font-size:5px;line-height:7px;color:var(--muted)}
  .footer-logo{position:absolute;right:3px;top:3px;width:48px;height:40px;background:var(--blue);
    display:flex;align-items:center;justify-content:center;text-align:center}
  .footer-logo .brand-name{font-size:8px;line-height:9px}

  .rule{position:absolute;left:8px;right:28px;top:15px;height:2px;background:var(--frame)}
  .rule-dot{position:absolute;left:6px;top:10px;width:13px;height:13px;border-radius:50%;background:var(--white);
    border:2px solid var(--frame)}
  .rule-dot::after{content:"";position:absolute;left:2px;top:2px;width:5px;height:5px;border-radius:50%;background:var(--blue)}

  .bullets{position:absolute;left:36px;top:31px;list-style:none}
  .bullet-main{font-family:var(--display);font-size:14px;color:var(--blue);display:flex;align-items:center;gap:6px}
  .bullet-sub{margin:6px 0 0 32px;font-size:8px;color:var(--ink);display:flex;align-items:center;gap:4px;font-family:var(--display)}
  .hex{display:inline-block;width:12px;height:12px}
  .hex--small{width:11px;height:11px}

  .chart{position:absolute;left:0;top:0}
</style>
</head>
<body>

  <!-- Title slide -->
  <div class="frame frame--title"></div>
  <section class="slide slide--title">
    <h1 class="title-heading">TITLE PAGE</h1>
    <p class="title-details">DETAILS OF PRESENTATION / NAME OF PRESENTOR</p>
    <div class="reflection" aria-hidden="true">
      <div class="title-heading">TITLE PAGE</div>
      <div class="title-details">DETAILS OF PRESENTATION / NAME OF PRESENTOR</div>
    </div>
    <div class="brand-circle"><span class="brand-name">Tarn Meridian</span></div>
    <p class="title-url">http://tarnmeridian-example.co.uk/</p>
    <div class="corner corner--br"><span>01</span></div>
  </section>

  <!-- Slide stack -->
  <div class="frame frame--stack"></div>

  <section class="slide slide--photo">
    <div class="photo" role="img" aria-label="Photograph: warm golden sunset over a meadow"></div>
    <div class="corner corner--tr"><span>02</span></div>
    <div class="footer-band" style="top:159px">
      <h2 class="footer-title">SLIDE TITLE</h2>
      <p class="footer-sub">DETAILS OF SLIDE / NAME OF PRESENTOR</p>
      <p class="footer-contact">www.tarnmeridian.com<br>info@tarnmeridian.com</p>
      <div class="footer-logo"><span class="brand-name">Tarn<br>Meridian</span></div>
    </div>
  </section>

  <section class="slide slide--bullets">
    <div class="rule"></div><div class="rule-dot"></div>
    <div class="corner corner--tr"><span>03</span></div>
    <ul class="bullets">
      <li class="bullet-main">
        <svg class="hex" viewBox="0 0 12 12"><polygon points="6,0.8 10.6,3.4 10.6,8.6 6,11.2 1.4,8.6 1.4,3.4" fill="none" stroke="var(--blue)" stroke-width="1.8"/></svg>
        MAIN BULLET</li>
      <li class="bullet-sub"><svg class="hex hex--small" viewBox="0 0 12 12"><polygon points="6,0.5 10.8,3.2 10.8,8.8 6,11.5 1.2,8.8 1.2,3.2" fill="var(--blue)" stroke="var(--frame)" stroke-width="1.2"/></svg>SUB BULLET FORM</li>
      <li class="bullet-sub"><svg class="hex hex--small" viewBox="0 0 12 12"><polygon points="6,0.5 10.8,3.2 10.8,8.8 6,11.5 1.2,8.8 1.2,3.2" fill="var(--blue)" stroke="var(--frame)" stroke-width="1.2"/></svg>SUB BULLET FORM</li>
      <li class="bullet-sub"><svg class="hex hex--small" viewBox="0 0 12 12"><polygon points="6,0.5 10.8,3.2 10.8,8.8 6,11.5 1.2,8.8 1.2,3.2" fill="var(--blue)" stroke="var(--frame)" stroke-width="1.2"/></svg>SUB BULLET FORM</li>
    </ul>
    <div class="footer-band" style="top:162px">
      <h2 class="footer-title">SLIDE TITLE</h2>
      <p class="footer-sub footer-sub--right">BULLET FORM</p>
      <p class="footer-contact">www.tarnmeridian.com<br>info@tarnmeridian.com</p>
      <div class="footer-logo"><span class="brand-name">Tarn<br>Meridian</span></div>
    </div>
  </section>

  <section class="slide slide--graphic">
    <div class="rule"></div><div class="rule-dot"></div>
    <div class="corner corner--tr"><span>04</span></div>
    <svg class="chart" width="380" height="160" viewBox="0 0 380 160" role="img" aria-label="Pyramid diagram and pie chart">
      <!-- pyramid -->
      <polygon points="102,62 81,86 123,86" fill="#8dc63f"/>
      <polygon points="79,89 125,89 152,113 52,113" fill="var(--blue)"/>
      <polygon points="52,113 152,113 155,116 49,116" fill="var(--blue-deep)"/>
      <polygon points="48,118 156,118 177,141 26,141" fill="#58595b"/>
      <polygon points="26,141 177,141 177,147 26,147" fill="#3a3a3c"/>
      <!-- pie -->
      <g transform="translate(217,40)">
        <ellipse cx="55" cy="62" rx="50" ry="50" fill="#2c3e50" opacity=".85"/>
        <g stroke="#fff" stroke-width="1.2">
          <path d="M55 55 L55 5 A50 50 0 0 1 94.1 23.8Z" fill="#3cb878"/>
          <path d="M55 55 L94.1 23.8 A50 50 0 0 1 103.7 66.2Z" fill="#16a99a"/>
          <path d="M55 55 L103.7 66.2 A50 50 0 0 1 76.7 100.1Z" fill="#27aae1"/>
          <path d="M55 55 L76.7 100.1 A50 50 0 0 1 33.3 100.1Z" fill="#c8a57a"/>
          <path d="M55 55 L33.3 100.1 A50 50 0 0 1 6.3 66.2Z" fill="#6d6e71"/>
          <path d="M55 55 L6.3 66.2 A50 50 0 0 1 15.9 23.8Z" fill="#8dc63f"/>
          <path d="M55 55 L15.9 23.8 A50 50 0 0 1 55 5Z" fill="#0f9547"/>
        </g>
      </g>
    </svg>
    <div class="footer-band" style="top:163px">
      <h2 class="footer-title">GRAPHIC SLIDE</h2>
      <p class="footer-sub">DETAILS OF SLIDE / NAME OF PRESENTOR</p>
      <p class="footer-contact">www.tarnmeridian.com<br>info@tarnmeridian.com</p>
      <div class="footer-logo"><span class="brand-name">Tarn<br>Meridian</span></div>
    </div>
  </section>

</body>
</html>
```